KorvaNest - Home Income and Business Resources Platform

I am looking for a website template for a multi-purposed website. This website will feature:

1.) Website Directory with Ratings & comments on listings
2.) Company Blog
3.) Homepage with Content (see files for homepage mock)

I would like the Design to have a default width 1170px (wider then normal)

Of course I am looking for Pages for Listings to be designed.

Great looking BLOG Layout: http://journal.plimworks.example/html/blog.html

I would like 4 Versions of a Website Directory Listing "Box"
1.) Basic Listing Box
2.) Sponsored Listing Box
3.) Recommended Listing Box
4.) Stay Away From Listing Box

Information on the Listing Page (Like on a Category Page)
Site Name, Site URL, Website Image, # of Views, Rating and # of Comments

Information on the Listing Details Page:
Same as ABOVE + About website Description, Vornic Score, Category Information

Decent looking examples is here: https://samples.trevolin.example/directory/computers/ and http://www.zqrankhub.example/.

I will include some sketches and screenshots of things I like/looking for. As designers,you have creative freedom and are encouraged to show this. This is Phase one of this project and winning designer is guaranteed to have future work for this project.

Target Market(s)

Directory, business, websites

Industry/Entity Type

Business

Coding

Coded - Design and coding required

Number of Pages Required

5+ page

Font styles to use
Sans Serif

Colors

Designer to choose colors to be used in the design.

Requirements
Must have
• Professional yet clean look. The use of Icons & images
• Unique Look
Should not have
• Any exact copies of any examples I provided

```html
<!DOCTYPE html>
<html lang="en">
<head>
<meta charset="utf-8">
<title>KorvaNest – Our Services</title>
<link href="https://fonts.googleapis.com/css2?family=Open+Sans:wght@400&family=Roboto:wght@300;400&family=Roboto+Condensed:wght@400;700&display=swap" rel="stylesheet">
<style>
  :root {
    --sky-light: #5cc6e0;
    --sky-mid: #3f95c4;
    --sky-deep: #2f6fa8;
    --card: #ffffff;
    --ink: #3a3a3a;
    --body-text: #4a4a4a;
    --green: #6ab614;
    --orange: #e89e38;
    --teal: #6cc0d9;
    --divider: #e6e6e6;
    --white: #ffffff;
  }
  * { margin: 0; padding: 0; box-sizing: border-box; }
  html, body { width: 926px; height: 1200px; overflow: hidden; }
  body { position: relative; font-family: "Open Sans", sans-serif; color: var(--ink); }

  .backdrop {
    position: absolute; inset: 0;
    background: linear-gradient(160deg, var(--sky-light) 0%, var(--sky-mid) 35%, var(--sky-deep) 60%, var(--sky-mid) 80%, var(--sky-light) 100%);
  }

  .brand {
    position: absolute; left: 76px; top: 26px;
    font-family: "Roboto", sans-serif; font-weight: 400; font-size: 30px;
    color: var(--white); letter-spacing: 0.5px;
  }

  .main-nav { position: absolute; top: 33px; left: 0; width: 926px; height: 24px; }
  .main-nav a {
    position: absolute; top: 0; height: 24px; line-height: 24px;
    font-family: "Roboto Condensed", sans-serif; font-size: 12.5px;
    color: var(--white); text-decoration: none; letter-spacing: 0.3px;
  }
  .main-nav a.is-current { border: 1px solid var(--white); border-radius: 3px; padding: 0 8px; }

  .content-card {
    position: absolute; left: 62px; top: 86px; width: 800px; height: 949px;
    background: var(--card); border-radius: 16px;
    box-shadow: 0 3px 8px rgba(0,0,0,0.2);
  }

  .page-banner {
    position: absolute; left: 76px; top: 100px; width: 774px; height: 177px;
    background: linear-gradient(100deg, #3a4a5e 0%, #6b6a6c 30%, #c08a4a 55%, #3c3a3c 80%, #2c3442 100%);
  }
  .page-title {
    position: absolute; left: 110px; top: 172px;
    font-family: "Roboto Condensed", sans-serif; font-weight: 700; font-size: 30px;
    color: var(--white); text-shadow: 0 1px 3px rgba(0,0,0,0.5);
  }

  .service-title {
    position: absolute; font-family: "Roboto", sans-serif; font-weight: 300;
    font-size: 20px; line-height: 24.5px; color: var(--ink);
  }
  .service-text {
    position: absolute; font-size: 8.6px; line-height: 16px; color: var(--body-text);
  }
  .align-right { text-align: right; }

  .service-badge { position: absolute; width: 190px; height: 190px; }

  .divider { position: absolute; left: 146px; width: 634px; height: 4px; }

  .social-row { position: absolute; top: 1088px; left: 396px; display: flex; gap: 10px; }
  .social-row span { width: 19px; height: 19px; background: var(--white); border-radius: 3px; display: block; }

  .footer-links {
    position: absolute; top: 1119px; left: 0; width: 926px; text-align: center;
    font-size: 10.5px; color: var(--white);
  }
  .footer-links a { color: var(--white); text-decoration: none; }
  .footer-links .sep { margin: 0 6px; }
  .copyright {
    position: absolute; top: 1143px; left: 0; width: 926px; text-align: center;
    font-size: 9.5px; color: var(--white);
  }
</style>
</head>
<body>
  <div class="backdrop" role="img" aria-label="Blue low-poly geometric background"></div>

  <div class="brand">KorvaNest</div>

  <nav class="main-nav">
    <a href="#" style="left:514px">HOME</a>
    <a href="#" style="left:565px">ABOUT US</a>
    <a href="#" class="is-current" style="left:630px">OUR SERVICES</a>
    <a href="#" style="left:737px">BLOG</a>
    <a href="#" style="left:785px">CONTACT US</a>
  </nav>

  <div class="content-card"></div>

  <div class="page-banner" role="img" aria-label="Photo of a business handshake at sunset beside a tablet showing a statistics chart"></div>
  <h1 class="page-title">OUR SERVICES</h1>

  <!-- Service: directory -->
  <h2 class="service-title align-right" style="right:380px; top:343px;">HOME INCOME<br>RESOURCE DIRECTORY</h2>
  <p class="service-text align-right" style="right:388px; top:406px; width:380px;">
    Find what you need, when you need it.The KorvaNest website directory is your one-stop pit for anything involved in making money from home, marketing your business or finding a new opportunity. Our modern, community supported directory will help you keep upto todate with the lastest information in a sensible fashion
  </p>
  <svg class="service-badge" style="left:579px; top:311px;" viewBox="0 0 190 190">
    <circle cx="95" cy="95" r="93" fill="none" stroke="#555" stroke-width="1.2" stroke-dasharray="0.1 6" stroke-linecap="round"/>
    <circle cx="95" cy="95" r="87" fill="var(--green)"/>
    <path d="M50 77 L95 42 L140 77" fill="none" stroke="#fff" stroke-width="8" stroke-linejoin="miter"/>
    <path d="M60 77 L95 50 L130 77 V137 H60 Z" fill="#fff"/>
    <circle cx="95" cy="102" r="20" fill="var(--green)"/>
    <text x="95" y="111" text-anchor="middle" font-family="Roboto, sans-serif" font-size="24" font-weight="400" fill="#fff">$</text>
  </svg>

  <svg class="divider" style="top:525px;" viewBox="0 0 634 4" preserveAspectRatio="none">
    <path d="M0 2 Q4 0 8 2 T16 2 T24 2 T32 2 T40 2 T48 2 T56 2 T64 2 T72 2 T80 2 T88 2 T96 2 T104 2 T112 2 T120 2 T128 2 T136 2 T144 2 T152 2 T160 2 T168 2 T176 2 T184 2 T192 2 T200 2 T208 2 T216 2 T224 2 T232 2 T240 2 T248 2 T256 2 T264 2 T272 2 T280 2 T288 2 T296 2 T304 2 T312 2 T320 2 T328 2 T336 2 T344 2 T352 2 T360 2 T368 2 T376 2 T384 2 T392 2 T400 2 T408 2 T416 2 T424 2 T432 2 T440 2 T448 2 T456 2 T464 2 T472 2 T480 2 T488 2 T496 2 T504 2 T512 2 T520 2 T528 2 T536 2 T544 2 T552 2 T560 2 T568 2 T576 2 T584 2 T592 2 T600 2 T608 2 T616 2 T624 2 T634 2" fill="none" stroke="var(--divider)" stroke-width="1.2"/>
  </svg>

  <!-- Service: advertising -->
  <svg class="service-badge" style="left:161px; top:555px;" viewBox="0 0 190 190">
    <circle cx="95" cy="95" r="93" fill="none" stroke="#555" stroke-width="1.2" stroke-dasharray="0.1 6" stroke-linecap="round"/>
    <circle cx="95" cy="95" r="87" fill="var(--orange)"/>
    <g fill="none" stroke="#fff" stroke-width="6" stroke-linejoin="round" stroke-linecap="round">
      <path d="M66 103 L98 62 L120 108 Z" fill="none"/>
      <path d="M108 60 Q118 66 119 78"/>
      <path d="M114 50 Q130 58 130 78"/>
    </g>
    <path d="M54 108 Q52 98 66 100 L72 120 Q58 122 54 108 Z" fill="#fff"/>
    <path d="M74 118 L88 116 L86 141 L78 141 Z" fill="#fff"/>
  </svg>
  <h2 class="service-title" style="left:382px; top:575px;">ADVERTISING<br>BENEFITS</h2>
  <p class="service-text" style="left:382px; top:630px; width:386px;">
    Everyone needs to advertise and we know just how to get your offer out to the right people. We have many methods including: Text ads, E-mail, Display, newsletter and even some old school methods available to make your next campaign a success. Advertise a website, a link text, full page circular or a small display ad and get results. Every advertiser recieves a dedicated account manager that will handle everything for You.
  </p>

  <svg class="divider" style="top:770px;" viewBox="0 0 634 4" preserveAspectRatio="none">
    <path d="M0 2 Q4 0 8 2 T16 2 T24 2 T32 2 T40 2 T48 2 T56 2 T64 2 T72 2 T80 2 T88 2 T96 2 T104 2 T112 2 T120 2 T128 2 T136 2 T144 2 T152 2 T160 2 T168 2 T176 2 T184 2 T192 2 T200 2 T208 2 T216 2 T224 2 T232 2 T240 2 T248 2 T256 2 T264 2 T272 2 T280 2 T288 2 T296 2 T304 2 T312 2 T320 2 T328 2 T336 2 T344 2 T352 2 T360 2 T368 2 T376 2 T384 2 T392 2 T400 2 T408 2 T416 2 T424 2 T432 2 T440 2 T448 2 T456 2 T464 2 T472 2 T480 2 T488 2 T496 2 T504 2 T512 2 T520 2 T528 2 T536 2 T544 2 T552 2 T560 2 T568 2 T576 2 T584 2 T592 2 T600 2 T608 2 T616 2 T624 2 T634 2" fill="none" stroke="var(--divider)" stroke-width="1.2"/>
  </svg>

  <!-- Service: earning -->
  <h2 class="service-title align-right" style="right:380px; top:839px;">EARNING WITH<br>KORVANEST</h2>
  <p class="service-text align-right" style="right:388px; top:901px; width:380px;">
    Join KorvaNest and start earning money. When you share KorvaNest and lock in an advertiser or premium listing, we reward you. Build a downline at any of our listed sites when you share KorvaNest with NO extra work. Its all done for you.We also offer a revenue share program for true supporters of our mission.
  </p>
  <svg class="service-badge" style="left:579px; top:807px;" viewBox="0 0 190 190">
    <circle cx="95" cy="95" r="93" fill="none" stroke="#555" stroke-width="1.2" stroke-dasharray="0.1 6" stroke-linecap="round"/>
    <circle cx="95" cy="95" r="87" fill="var(--teal)"/>
    <rect x="48" y="115" width="18" height="24" rx="2" fill="#fff"/>
    <rect x="72" y="100" width="18" height="39" rx="2" fill="#fff"/>
    <rect x="97" y="85" width="18" height="54" rx="2" fill="#fff"/>
    <path d="M49 100 L90 78" stroke="#fff" stroke-width="4" stroke-linecap="round"/>
    <path d="M82 72 L96 75 L88 86 Z" fill="#fff"/>
    <circle cx="106" cy="66" r="12" fill="#fff"/>
    <text x="106" y="72" text-anchor="middle" font-family="Roboto, sans-serif" font-size="16" fill="var(--teal)">$</text>
  </svg>

  <!-- Footer -->
  <div class="social-row" aria-label="Social profiles">
    <span></span><span></span><span></span><span></span><span></span>
  </div>
  <div class="footer-links">
    <a href="#">Home</a><span class="sep">/</span><a href="#">Contact</a><span class="sep">/</span><a href="#">services</a><span class="sep">/</span><a href="#">About Us</a><span class="sep">/</span><a href="#">Discussion</a><span class="sep">/</span><a href="#">Videos Links</a>
  </div>
  <div class="copyright">Copyright @ 2017 KorvaNest. All Rights Reserved.</div>
</body>
</html>
```